Corvane Lending Partners. Professional and Established Company

A full service finance company specializing in obtaining capital for small business. Business Lending advisor, helping small business owners access the capital they need to launch, grow, or sustain their business. Many of our programs offer flexible guidelines to overcome common obstacles such as credit score, credit history, and time in business, financials, and industry type. Our streamlined funding process makes getting a business loan, business line of credit, stated income commercial real estate loan, a smooth and stress free experience.SOME OF THE MOST COMMON NEEDS FOR BUSINESS CAPITAL:• Working Capital• Debt Consolidations (loans, merchant cash advances, etc.)• Payroll• Operating Expenses• Inventory• Equipment Financing• Commercial Real Estate (Purchase, Fix & Flip, Rehab, Renovations)• Business Acquisitions• Business ExpansionWe like the websites:www.quillmorecf.com they are in the same industry and provide the same servicesWe are wanting to be able to update when we do press releases and such using Word Press. Our look should be very professional and we will be adding Our Team Professional Bios and Headshots.

Industry/Entity Type

Finance

Number of Pages Required

5+ page

Font styles to use
Serif
Sans Serif

Requirements
Must have
• We want to copy quillmorecf.com
• We need:
• Home Page
• About Us
• Loan Programs
• Loan Criteria
• News
• Apply Now
• Contact
Nice to have
• See quillmorecf.com
Should not have
• Need professional design. Nothing bright or abstract

```html
<!DOCTYPE html>
<html lang="en">
<head>
<meta charset="utf-8">
<title>Corvane Lending Partners</title>
<link href="https://fonts.googleapis.com/css2?family=Cinzel:wght@400;600;700&family=Montserrat:wght@400;500;600;700&display=swap" rel="stylesheet">
<style>
:root{
  --blue:#1f6fc0;
  --blue-dark:#12508f;
  --blue-soft:#2d82d6;
  --ink:#2b2b2b;
  --muted:#555b63;
  --grey-bg:#ececec;
  --line:#d9d9d9;
  --white:#ffffff;
}
*{box-sizing:border-box;margin:0;padding:0}
html,body{width:1200px;height:3495px;overflow:hidden;background:var(--white)}
body{position:relative;font-family:"Montserrat",Arial,sans-serif;color:var(--ink)}
.abs{position:absolute}
a{color:inherit;text-decoration:none}

/* header */
.brand{left:112px;top:38px;display:flex;align-items:center;gap:10px;color:var(--blue);font-family:"Montserrat",Arial,sans-serif;font-weight:600;font-size:22px;line-height:26px;white-space:nowrap}
.brand-mark{width:14px;height:14px;background:var(--blue);border-radius:50%}
.contact{top:20px;right:112px;display:flex;gap:28px;font-size:17px;color:var(--blue);font-weight:500}
.contact span{display:flex;align-items:center;gap:8px}
.main-nav{top:72px;right:112px;display:flex;gap:25px;font-size:16px;font-weight:500;color:var(--ink)}

/* hero */
.hero{left:0;top:116px;width:1200px;height:560px;background:linear-gradient(100deg,#3b4452 0%,#5d6a79 40%,#8e8a86 62%,#76797d 80%,#4d5968 100%)}
.hero-title{left:112px;top:205px;font-family:"Cinzel",Georgia,serif;font-size:76px;color:var(--white);font-weight:400;letter-spacing:2px}
.hero-lead{left:112px;top:310px;width:500px;font-size:19px;line-height:28px;color:var(--white);font-weight:500}
.dots{left:112px;top:396px;display:flex;gap:8px}
.dots i{width:16px;height:16px;border-radius:50%;background:rgba(255,255,255,.55)}
.dots i:first-child{background:var(--white)}
.criteria{left:0;top:500px;width:1200px;height:176px;background:linear-gradient(90deg,rgba(18,80,143,.92),rgba(31,111,192,.92) 55%,rgba(45,130,214,.9));display:flex;padding-left:98px}
.crit{width:210px;text-align:center;color:var(--white);padding-top:26px;border-left:1px solid rgba(255,255,255,.45)}
.crit:first-child{border-left:none}
.crit h3{font-size:18px;font-weight:600;margin-top:8px}
.crit p{font-size:13px;line-height:18px;margin:10px auto 0;width:150px}

/* section headings */
.sec-title{left:0;width:1200px;text-align:center;font-family:"Cinzel",Georgia,serif;font-weight:600;font-size:36px;color:var(--blue);letter-spacing:1px}
.rule{left:550px;width:100px;height:3px;background:var(--blue)}

/* services */
.svc{width:330px}
.svc h4{font-size:20px;font-weight:600;color:var(--ink)}
.svc h4.hl{color:var(--blue)}
.svc p{font-size:14px;line-height:20px;color:var(--muted);margin-top:6px}
.svc.left{text-align:right}
.icon-ring{width:60px;height:60px;border-radius:50%;border:2px solid var(--blue);display:flex;align-items:center;justify-content:center;background:var(--white)}
.icon-ring.dark{border-color:#555}
.figure{left:478px;top:900px;width:244px;height:370px;border-radius:8px;background:linear-gradient(180deg,#e7e2d8 0%,#d8cfb8 45%,#a9b2c0 80%,#c9c9c9 100%)}
.figure-shadow{left:365px;top:1262px;width:470px;height:20px;border-radius:50%;background:#c4c4c4}

/* loans */
.photo-desk{left:427px;top:1383px;width:773px;height:343px;background:linear-gradient(110deg,#6d6d6d,#b9b9b9 40%,#e6e6e6 70%,#8a8a8a)}
.photo-data{left:0;top:1735px;width:770px;height:343px;background:linear-gradient(120deg,#1c2a3b,#5a6e86 45%,#2a3b52 80%,#18212e)}
.loan-box{background:var(--blue);color:var(--white);text-align:center;padding:50px 36px;outline:4px solid var(--white)}
.loan-box h3{font-size:27px;font-weight:600;margin-top:14px}
.loan-box p{font-size:15px;line-height:25px;margin-top:18px}

/* team */
.member{width:237px;top:2297px}
.member .photo{height:180px;background:linear-gradient(160deg,#cfcfcf,#8c8c8c)}
.member h4{font-size:22px;font-weight:700;color:#333;margin-top:28px;text-transform:uppercase}
.member .role{font-size:15px;font-weight:600;color:#444;margin-top:10px}
.member .bar{width:78px;height:4px;background:var(--blue);margin-top:16px}
.member-hover{width:237px;top:2297px;height:286px;background:var(--blue);color:var(--white);text-align:center;font-size:15px;line-height:24px;padding:46px 20px}

/* blog */
.blog-bg{left:0;top:2680px;width:1200px;height:655px;background:var(--grey-bg)}
.post{top:2863px;width:303px;height:383px;background:var(--white);box-shadow:0 2px 6px rgba(0,0,0,.15)}
.post .thumb{height:168px;background:linear-gradient(135deg,#4c5966,#c9d0d6 55%,#7c8894)}
.post h4{font-size:17px;font-weight:700;text-align:center;margin-top:28px;letter-spacing:.5px}
.post p{font-size:13px;line-height:21px;color:var(--muted);text-align:center;padding:0 20px;margin-top:14px}
.post .meta{position:absolute;left:12px;right:12px;bottom:0;height:70px;border-top:1px solid var(--line);display:flex;align-items:center;justify-content:center;gap:10px;font-size:16px}
.avatar{width:40px;height:40px;border-radius:50%;background:#b89a85}

/* footer */
.foot-brand{top:3400px}
.foot-nav{right:112px;top:3382px;display:flex;gap:24px;font-size:14px;font-weight:500}
.foot-rule{left:435px;top:3423px;width:653px;height:1px;background:var(--line)}
.copyright{right:112px;top:3452px;font-size:13px;font-weight:500}
</style>
</head>
<body>

<!-- header -->
<div class="abs brand"><span class="brand-mark"></span>Corvane Lending Partners</div>
<div class="abs contact">
  <span><svg width="30" height="30" viewBox="0 0 30 30"><circle cx="15" cy="15" r="13" fill="none" stroke="#1f6fc0" stroke-width="2"/><path d="M10 9c1-1 2-1 3 1l1 2c0 1-1 1-1 2 1 2 2 3 4 4 1 0 1-1 2-1l2 1c2 1 2 2 1 3-2 2-5 1-8-2s-5-7-4-10z" fill="#1f6fc0"/></svg>+1800555014</span>
  <span><svg width="30" height="30" viewBox="0 0 30 30"><circle cx="15" cy="15" r="13" fill="none" stroke="#1f6fc0" stroke-width="2"/><rect x="8" y="10" width="14" height="10" fill="none" stroke="#1f6fc0" stroke-width="1.8"/><path d="M8 10l7 6 7-6" fill="none" stroke="#1f6fc0" stroke-width="1.8"/></svg>info@corvanelending.com</span>
</div>
<nav class="abs main-nav">
  <a>Home</a><a>About Us</a><a>Loan Programs</a><a>Loan Criteria</a><a>News</a><a>Apply Now</a><a>Contact</a>
</nav>

<!-- hero -->
<div class="abs hero" role="img" aria-label="Young businesswoman smiling while holding a phone on a busy city street"></div>
<h1 class="abs hero-title">CORVANE</h1>
<p class="abs hero-lead">We are a full service finance company specializing in obtaining capital for small business.</p>
<div class="abs dots"><i></i><i></i><i></i><i></i><i></i></div>

<div class="abs criteria">
  <div class="crit">
    <svg width="40" height="40" viewBox="0 0 40 40" fill="none" stroke="#fff" stroke-width="2"><rect x="12" y="6" width="16" height="26" rx="2"/><path d="M16 14h8M16 19h8M16 24h5"/></svg>
    <h3>Credit Score</h3><p>Duis aute irure dolor in reprehenderit.</p>
  </div>
  <div class="crit">
    <svg width="40" height="40" viewBox="0 0 40 40" fill="none" stroke="#fff" stroke-width="2"><rect x="6" y="6" width="20" height="26"/><path d="M10 13h12M10 18h12M10 23h8"/><path d="M28 20l6 10M34 20l-6 10"/></svg>
    <h3>Credit History</h3><p>Duis aute irure dolor in reprehenderit.</p>
  </div>
  <div class="crit">
    <svg width="40" height="40" viewBox="0 0 40 40" fill="none" stroke="#fff" stroke-width="2"><rect x="6" y="10" width="28" height="22" rx="2"/><path d="M6 17h28M13 6v7M27 6v7"/><circle cx="20" cy="25" r="4"/></svg>
    <h3>Time In Business</h3><p>Duis aute irure dolor in reprehenderit.</p>
  </div>
  <div class="crit">
    <svg width="40" height="40" viewBox="0 0 40 40" fill="none" stroke="#fff" stroke-width="2"><rect x="8" y="6" width="24" height="28" rx="2"/><path d="M13 26v-5M19 26v-9M25 26v-13"/></svg>
    <h3>Financials</h3><p>Duis aute irure dolor in reprehenderit.</p>
  </div>
  <div class="crit">
    <svg width="40" height="40" viewBox="0 0 40 40" fill="none" stroke="#fff" stroke-width="2"><path d="M6 32h28M9 32V22M17 32V16M25 32V20M33 32V10"/><path d="M8 18l8-8 7 5 10-9"/></svg>
    <h3>Industry Type</h3><p>Duis aute irure dolor in reprehenderit.</p>
  </div>
</div>

<!-- services -->
<h2 class="abs sec-title" style="top:752px">Services We Provide</h2>
<div class="abs rule" style="top:818px"></div>

<div class="abs figure-shadow"></div>
<div class="abs figure" role="img" aria-label="Woman in a yellow top sitting cross-legged with a laptop"></div>

<div class="abs svc left" style="left:60px;top:884px"><h4 class="hl">Working Capital</h4><p>Duis aute irure dolor in reprehenderit in voluptate velit esse cillum.</p></div>
<div class="abs svc left" style="left:42px;top:978px"><h4>Debt Consolidations</h4><p>Duis aute irure dolor voluptate in reprehenderit in voluptate.</p></div>
<div class="abs svc left" style="left:25px;top:1072px"><h4 class="hl">Payroll</h4><p>Duis aute irure dolor voluptate in reprehenderit.</p></div>
<div class="abs svc left" style="left:9px;top:1166px"><h4>Operating Expenses</h4><p>Duis aute irure dolor voluptate in reprehenderit</p></div>

<div class="abs icon-ring" style="left:403px;top:886px"><svg width="30" height="30" viewBox="0 0 30 30" fill="none" stroke="#1f6fc0" stroke-width="2"><circle cx="15" cy="10" r="5"/><path d="M6 26c0-6 4-9 9-9s9 3 9 9z"/></svg></div>
<div class="abs icon-ring dark" style="left:385px;top:981px"><svg width="30" height="30" viewBox="0 0 30 30" fill="none" stroke="#555" stroke-width="2"><circle cx="15" cy="8" r="3"/><circle cx="7" cy="18" r="3"/><circle cx="23" cy="18" r="3"/><path d="M3 27h24"/></svg></div>
<div class="abs icon-ring" style="left:368px;top:1074px"><svg width="30" height="30" viewBox="0 0 30 30" fill="none" stroke="#1f6fc0" stroke-width="2"><rect x="7" y="5" width="16" height="20" rx="2"/><circle cx="15" cy="15" r="4"/></svg></div>
<div class="abs icon-ring dark" style="left:352px;top:1168px"><svg width="30" height="30" viewBox="0 0 30 30" fill="none" stroke="#555" stroke-width="2"><rect x="5" y="5" width="16" height="20"/><path d="M9 11h8M9 16h8"/><path d="M20 18l6 8M26 18l-6 8"/></svg></div>

<div class="abs icon-ring dark" style="left:732px;top:886px"><svg width="30" height="30" viewBox="0 0 30 30" fill="none" stroke="#555" stroke-width="2"><rect x="7" y="5" width="16" height="20" rx="2"/><path d="M11 12h8M11 17h6"/></svg></div>
<div class="abs icon-ring" style="left:748px;top:981px"><svg width="30" height="30" viewBox="0 0 30 30" fill="none" stroke="#1f6fc0" stroke-width="2"><circle cx="9" cy="10" r="3"/><circle cx="21" cy="10" r="3"/><path d="M4 24c0-5 2-8 5-8s5 3 5 8M16 24c0-5 2-8 5-8s5 3 5 8"/></svg></div>
<div class="abs icon-ring dark" style="left:765px;top:1074px"><svg width="30" height="30" viewBox="0 0 30 30" fill="none" stroke="#555" stroke-width="2"><rect x="7" y="5" width="16" height="20" rx="2"/><path d="M11 21v-4M15 21v-7M19 21v-10"/></svg></div>
<div class="abs icon-ring" style="left:781px;top:1168px"><svg width="30" height="30" viewBox="0 0 30 30" fill="none" stroke="#1f6fc0" stroke-width="2"><rect x="6" y="8" width="18" height="16" rx="2"/><path d="M11 8V5h8v3M15 13v6M12 16h6"/></svg></div>

<div class="abs svc" style="left:808px;top:884px"><h4>Inventory</h4><p>Duis aute irure dolor in reprehenderit in voluptate velit esse cillum.</p></div>
<div class="abs svc" style="left:825px;top:978px"><h4 class="hl">Equipment Financing</h4><p>Duis aute irure dolor voluptate in reprehenderit in voluptate.</p></div>
<div class="abs svc" style="left:842px;top:1072px"><h4>Business Acquisitions</h4><p>Duis aute irure dolor voluptate in reprehenderit.</p></div>
<div class="abs svc" style="left:860px;top:1166px"><h4 class="hl">Business Expansion</h4><p>Duis aute irure dolor voluptate in reprehenderit</p></div>

<!-- loan programs -->
<div class="abs photo-desk" role="img" aria-label="Hand signing a loan document on a desk"></div>
<div class="abs loan-box" style="left:0;top:1398px;width:450px;height:310px">
  <svg width="70" height="66" viewBox="0 0 70 66" fill="none" stroke="#fff" stroke-width="3"><circle cx="40" cy="22" r="17"/><path d="M45 15c-2-2-9-3-9 2s10 3 10 8-8 4-10 2M40 10v4M40 30v4"/><path d="M4 46h12l10 6h14c3 0 3 4 0 4H28M16 58l14 4 30-12c3-1 1-5-2-4L44 52"/></svg>
  <h3>Business Loan</h3>
  <p>Nemo enim ipsam voluptatem quia voluptas sit aspernatur aut odit aut fugit, sed quia consequuntur magni dolores.</p>
</div>

<div class="abs photo-data" role="img" aria-label="Hand touching a digital display of financial charts and a world map"></div>
<div class="abs loan-box" style="left:748px;top:1750px;width:452px;height:310px">
  <svg width="66" height="66" viewBox="0 0 66 66" fill="none" stroke="#fff" stroke-width="3"><path d="M24 6h14l-4 10h-6z"/><path d="M28 16c-14 8-18 24-14 32 3 6 10 8 16 8"/><path d="M34 16c8 5 12 12 13 20"/><ellipse cx="48" cy="42" rx="12" ry="4"/><path d="M36 42v8c0 2 5 4 12 4s12-2 12-4v-8M36 50v6c0 2 5 4 12 4s12-2 12-4v-6"/></svg>
  <h3>Real Estate Loan</h3>
  <p>Nemo enim ipsam voluptatem quia voluptas sit aspernatur aut odit aut fugit, sed quia consequuntur magni dolores.</p>
</div>

<!-- team -->
<h2 class="abs sec-title" style="top:2162px">Our Team Professionals</h2>
<div class="abs rule" style="top:2228px"></div>

<div class="abs member" style="left:112px">
  <div class="photo" role="img" aria-label="Headshot of team member Owen Hartley"></div>
  <h4>Owen Hartley</h4><div class="role">Nemo Enim</div><div class="bar"></div>
</div>
<div class="abs member" style="left:357px">
  <div class="photo" role="img" aria-label="Headshot of team member Lena Brooks"></div>
  <h4>Lena Brooks</h4><div class="role">Nemo Enim</div><div class="bar"></div>
</div>
<div class="abs member-hover" style="left:603px">
  Nemo enim ipsam voluptatem quia voluptas sit aspernatur aut odit aut fugit, sed quia consequuntur magni dolores eos qui ratione voluptatem sequi nesciunt.
</div>
<div class="abs member" style="left:850px">
  <div class="photo" role="img" aria-label="Headshot of team member Paul Dorran"></div>
  <h4>Paul Dorran</h4><div class="role">Nemo Enim</div><div class="bar"></div>
</div>

<!-- blog -->
<div class="abs blog-bg"></div>
<h2 class="abs sec-title" style="top:2740px">Our Blog Posts</h2>
<div class="abs rule" style="top:2806px"></div>

<article class="abs post" style="left:112px">
  <div class="thumb" role="img" aria-label="Business team meeting around a table"></div>
  <h4>NEMO ENIM IPSAM</h4>
  <p>Sed ut perspiciatis unde omnis iste natus error sit voluptatem accusantium dolo remque laudantium.</p>
  <div class="meta"><span class="avatar" role="img" aria-label="Author avatar"></span><svg width="18" height="16" viewBox="0 0 18 16"><path d="M9 15S1 10 1 5a4 4 0 0 1 8-1 4 4 0 0 1 8 1c0 5-8 10-8 10z" fill="none" stroke="#333" stroke-width="1.6"/></svg><svg width="22" height="16" viewBox="0 0 22 16" fill="#333"><circle cx="6" cy="4" r="3"/><circle cx="16" cy="4" r="3"/><path d="M0 15c0-4 3-6 6-6s6 2 6 6zM10 15c0-4 3-6 6-6s6 2 6 6z"/></svg><span>2</span></div>
</article>
<article class="abs post" style="left:450px">
  <div class="thumb" role="img" aria-label="Colleagues discussing work at a desk"></div>
  <h4>NEMO ENIM IPSAM</h4>
  <p>Sed ut perspiciatis unde omnis iste natus error sit voluptatem accusantium dolo remque laudantium.</p>
  <div class="meta"><span class="avatar" role="img" aria-label="Author avatar"></span><svg width="18" height="16" viewBox="0 0 18 16"><path d="M9 15S1 10 1 5a4 4 0 0 1 8-1 4 4 0 0 1 8 1c0 5-8 10-8 10z" fill="none" stroke="#333" stroke-width="1.6"/></svg><svg width="22" height="16" viewBox="0 0 22 16" fill="#333"><circle cx="6" cy="4" r="3"/><circle cx="16" cy="4" r="3"/><path d="M0 15c0-4 3-6 6-6s6 2 6 6zM10 15c0-4 3-6 6-6s6 2 6 6z"/></svg><span>2</span></div>
</article>
<article class="abs post" style="left:786px">
  <div class="thumb" role="img" aria-label="Boardroom presentation in a bright office"></div>
  <h4>NEMO ENIM IPSAM</h4>
  <p>Sed ut perspiciatis unde omnis iste natus error sit voluptatem accusantium dolo remque laudantium.</p>
  <div class="meta"><span class="avatar" role="img" aria-label="Author avatar"></span><svg width="18" height="16" viewBox="0 0 18 16"><path d="M9 15S1 10 1 5a4 4 0 0 1 8-1 4 4 0 0 1 8 1c0 5-8 10-8 10z" fill="none" stroke="#333" stroke-width="1.6"/></svg><svg width="22" height="16" viewBox="0 0 22 16" fill="#333"><circle cx="6" cy="4" r="3"/><circle cx="16" cy="4" r="3"/><path d="M0 15c0-4 3-6 6-6s6 2 6 6zM10 15c0-4 3-6 6-6s6 2 6 6z"/></svg><span>2</span></div>
</article>

<!-- footer -->
<div class="abs brand foot-brand"><span class="brand-mark"></span>Corvane Lending Partners</div>
<nav class="abs foot-nav">
  <a>Home</a><a>About Us</a><a>Loan Programs</a><a>Loan Criteria</a><a>News</a><a>Apply Now</a><a>Contact</a>
</nav>
<div class="abs foot-rule"></div>
<p class="abs copyright">Copyrights @ 2018 Corvane. All Rights Reserved.</p>

</body>
</html>
```